Brickfield real estate investment company needs a poster design

We would like a poster design size 18 x 24.
Poster wording -
I WANT TO BUY YOUR ( finish with logo) logo uploaded
website- www.brickfield.example
phone # 555-218-7043 ( color red for the phone number)
we would like to see the poster on 2 different backgrounds
Yellow background
White background
horizontal

```html
<!DOCTYPE html>
<html lang="en">
<head>
<meta charset="utf-8">
<title>Brickfield — I Want To Buy Your House</title>
<link rel="stylesheet" href="https://fonts.googleapis.com/css2?family=Luckiest+Guy&family=Caveat+Brush&display=swap">
<style>
  :root{
    --red:#ee1c2e;
    --ink:#0d0d0d;
    --yellow:#f7e872;
    --yellow-soft:#f6ee9c;
    --paper:#f4f4f4;
    --grey:#c9c9c9;
    --url:#1a1a1a;
    --icon-grey:#8a8a8a;
  }
  *{margin:0;padding:0;box-sizing:border-box}
  html,body{width:900px;height:1200px;overflow:hidden;background:#fff}
  .poster{
    position:relative;width:900px;height:1200px;overflow:hidden;
    background:linear-gradient(180deg,#fafafa 0%,var(--paper) 40%,#e2e2e2 70%,var(--grey) 100%);
    font-family:"Luckiest Guy","Arial Black",Impact,sans-serif;
  }
  .house-backdrop{
    position:absolute;left:70px;top:60px;width:800px;height:1000px;
    background:linear-gradient(180deg,rgba(246,238,156,.55) 0%,rgba(246,238,156,.35) 60%,rgba(246,238,156,.15) 100%);
    clip-path:polygon(0 28%,50% 0,100% 24%,100% 100%,0 100%);
  }
  .site{position:absolute;top:18px;left:14px;display:flex;align-items:center;gap:18px}
  .site__icon{width:50px;height:50px}
  .site__url{font-family:Arial,Helvetica,sans-serif;font-size:36px;letter-spacing:.28em;color:var(--url);white-space:nowrap}
  .cursor{position:absolute;top:54px;right:14px;width:50px;height:50px}

  .headline{position:absolute;inset:0;font-weight:400}
  .headline__line{
    position:absolute;left:0;width:900px;text-align:center;white-space:nowrap;line-height:1;
    text-shadow:2px 3px 4px rgba(0,0,0,.18);
  }
  .line-want{top:190px;font-size:112px;color:var(--ink);padding-right:60px;transform:rotate(-9deg)}
  .line-want .accent{color:var(--red);margin-right:.2em}
  .line-buy{top:325px;font-size:150px;color:var(--red);padding-right:30px;transform:rotate(-12deg)}
  .line-your{top:515px;font-size:112px;color:var(--ink);padding-left:50px;transform:rotate(-7deg)}

  .band{
    position:absolute;left:-30px;top:668px;width:960px;height:290px;background:var(--yellow);
    transform:rotate(-2deg);
  }
  .brand{
    position:absolute;left:0;width:900px;top:752px;display:flex;align-items:center;justify-content:center;gap:20px;
    transform:rotate(-3deg);
  }
  .brand__mark{width:38px;height:38px;background:var(--red);border-radius:50%;flex:none}
  .brand__name{font-size:96px;color:var(--ink);line-height:1;padding-top:12px;white-space:nowrap}

  .phone{position:absolute;left:0;right:0;bottom:24px;display:flex;align-items:center;justify-content:center;gap:14px}
  .phone__icon{width:72px;height:72px;flex:none}
  .phone__number{font-family:"Caveat Brush",cursive;font-size:100px;color:var(--red);line-height:1;letter-spacing:.03em;white-space:nowrap}
</style>
</head>
<body>
<div class="poster">
  <div class="house-backdrop" role="img" aria-label="Large faint house shape behind the headline"></div>

  <div class="site">
    <svg class="site__icon" viewBox="0 0 52 52" aria-hidden="true">
      <circle cx="26" cy="26" r="22" fill="#e9e9e9" stroke="var(--icon-grey)" stroke-width="3"/>
      <ellipse cx="26" cy="26" rx="10" ry="22" fill="none" stroke="var(--icon-grey)" stroke-width="3"/>
      <line x1="4" y1="26" x2="48" y2="26" stroke="var(--icon-grey)" stroke-width="3"/>
      <line x1="8" y1="15" x2="44" y2="15" stroke="var(--icon-grey)" stroke-width="3"/>
      <line x1="8" y1="37" x2="44" y2="37" stroke="var(--icon-grey)" stroke-width="3"/>
    </svg>
    <span class="site__url">www.brickfield.example</span>
  </div>

  <svg class="cursor" viewBox="0 0 52 52" aria-hidden="true">
    <path d="M6 4 L44 30 L28 31 L36 47 L29 50 L21 34 L9 44 Z" fill="#f4f4f4" stroke="#a8a8a8" stroke-width="3" stroke-linejoin="round"/>
  </svg>

  <h1 class="headline">
    <span class="headline__line line-want"><span class="accent">I</span>WANT</span>
    <span class="headline__line line-buy">TO BUY</span>
    <span class="headline__line line-your">YOUR</span>
  </h1>

  <div class="band"></div>
  <div class="brand">
    <span class="brand__mark"></span>
    <span class="brand__name">BRICKFIELD</span>
  </div>

  <div class="phone">
    <svg class="phone__icon" viewBox="0 0 74 74" aria-hidden="true">
      <circle cx="37" cy="37" r="32" fill="none" stroke="var(--red)" stroke-width="6"/>
      <path d="M24 20 c3-2 6-2 7 1 l3 7 c1 2 0 4-2 5 l-2 2 c2 5 6 9 11 11 l2-2 c1-2 3-3 5-2 l7 3 c3 1 3 4 1 7 l-3 3 c-4 3-12 1-20-7 s-11-17-7-22 Z" fill="none" stroke="var(--red)" stroke-width="5" stroke-linejoin="round"/>
    </svg>
    <span class="phone__number">555-218-7043</span>
  </div>
</div>
</body>
</html>
```